Business Card Design

We are looking for a business card designed for our landscaping company. We do landscaping installation & Maintenance Services. We would like to see designs that have basic landscaping in background. We also think it is important to have both of our names and phone numbers on the card. We need something that stands out a little whether it is shape of the card or thickness or design.

Business

Bramblewood Yardworks, bramblewoodyard@mailvista.net, Owen Platt 555-273-9104, Daniel Korbin 555-618-3927

```html
<!DOCTYPE html>
<html lang="en">
<head>
<meta charset="utf-8">
<title>Bramblewood Yardworks – Business Card</title>
<link rel="stylesheet" href="https://fonts.googleapis.com/css2?family=Bodoni+Moda:wght@600;700&family=Open+Sans:wght@400&display=swap">
<style>
  :root {
    --page-bg: #e9e6e1;
    --card-white: #f4f4f4;
    --brand-green: #1f9a35;
    --ink-black: #050505;
    --text-dark: #161616;
    --text-light: #f2f2f2;
    --divider: #dcdcdc;
  }
  html, body {
    margin: 0;
    width: 1200px;
    height: 902px;
    overflow: hidden;
    background: var(--page-bg);
  }
  .card {
    position: absolute;
    left: 100px;
    top: 165px;
    width: 1000px;
    height: 572px;
    box-shadow: 0 10px 30px rgba(0,0,0,0.18);
    overflow: hidden;
  }
  .card-shapes {
    position: absolute;
    inset: 0;
  }
  .company-name {
    position: absolute;
    left: 0;
    right: 0;
    top: 118px;
    margin: 0;
    text-align: center;
    font-family: "Bodoni Moda", "Didot", serif;
    font-weight: 700;
    font-size: 58px;
    letter-spacing: 0.5px;
    color: var(--text-dark);
  }
  .company-email {
    position: absolute;
    left: 0;
    right: 0;
    top: 208px;
    margin: 0;
    text-align: center;
    font-family: "Open Sans", Arial, sans-serif;
    font-size: 24px;
    color: var(--text-dark);
  }
  .contacts {
    position: absolute;
    left: 62px;
    top: 386px;
    color: var(--text-light);
  }
  .contact-name {
    margin: 0;
    font-family: "Bodoni Moda", "Didot", serif;
    font-weight: 600;
    font-size: 38px;
    line-height: 46px;
  }
  .contact-phone {
    display: flex;
    align-items: center;
    gap: 12px;
    margin: 0 0 10px 8px;
    font-family: "Open Sans", Arial, sans-serif;
    font-size: 27px;
    line-height: 36px;
  }
  .phone-icon {
    width: 22px;
    height: 22px;
  }
</style>
</head>
<body>
  <div class="card">
    <svg class="card-shapes" width="1000" height="572" viewBox="0 0 1000 572" aria-hidden="true">
      <rect class="card-face" width="1000" height="572" fill="var(--card-white)"/>
      <polygon class="green-field" points="0,332 1000,228 1000,572 0,572" fill="var(--brand-green)"/>
      <polygon class="black-panel" points="0,350 694,278 728,572 0,572" fill="var(--ink-black)"/>
      <line class="panel-divider" x1="698" y1="278" x2="732" y2="572" stroke="var(--divider)" stroke-width="3"/>
    </svg>

    <h1 class="company-name">Bramblewood Yardworks</h1>
    <p class="company-email">bramblewoodyard@mailvista.net</p>

    <div class="contacts">
      <p class="contact-name">Owen Platt</p>
      <p class="contact-phone">
        <svg class="phone-icon" viewBox="0 0 22 22" aria-hidden="true">
          <rect width="22" height="22" rx="2" fill="var(--text-light)"/>
          <path d="M7 4.5c-1.3 .6-2 1.8-1.6 3.5 1 4 4.5 8 8.3 9.3 1.6 .5 3-.2 3.6-1.4l-2.6-2.2-1.7 1c-1.8-.9-3.7-3-4.5-4.9l1.1-1.6z" fill="var(--ink-black)"/>
        </svg>
        555-273-9104
      </p>
      <p class="contact-name">Daniel Korbin</p>
      <p class="contact-phone">
        <svg class="phone-icon" viewBox="0 0 22 22" aria-hidden="true">
          <rect width="22" height="22" rx="2" fill="var(--text-light)"/>
          <path d="M7 4.5c-1.3 .6-2 1.8-1.6 3.5 1 4 4.5 8 8.3 9.3 1.6 .5 3-.2 3.6-1.4l-2.6-2.2-1.7 1c-1.8-.9-3.7-3-4.5-4.9l1.1-1.6z" fill="var(--ink-black)"/>
        </svg>
        555-618-3927
      </p>
    </div>
  </div>
</body>
</html>
```